New Business Card Design Project

Use the flyer uploaded and website www.brightoakbuilders.com for inspiration.
List Our Services on Backside of business cards
Marcus Delling
Harborline Builders Inc.
Licensed General Contractors
858-471-6093

Contact Information for Business Card

Use the flyer uploaded and website www.brightoakbuilders.com for inspiration. List Our Services on Backside of business cards Marcus Delling Harborline Builders Inc. Licensed General Contractors 858-471-6093

```html
<!DOCTYPE html>
<html lang="en">
<head>
<meta charset="utf-8">
<title>Harborline Builders – Business Card</title>
<link href="https://fonts.googleapis.com/css2?family=Montserrat:wght@400;600;700;800&display=swap" rel="stylesheet">
<style>
  :root {
    --page: #3a3a3a;
    --card: #121212;
    --ink: #ffffff;
    --shadow: rgba(0,0,0,0.55);
  }
  * { box-sizing: border-box; margin: 0; padding: 0; }
  html, body { width: 1200px; height: 998px; overflow: hidden; }
  body {
    background: var(--page);
    font-family: "Montserrat", sans-serif;
    color: var(--ink);
    position: relative;
  }
  .card {
    position: absolute;
    left: 220px;
    width: 760px;
    height: 434px;
    background: var(--card);
    box-shadow: 0 12px 30px var(--shadow);
  }
  .card--back { top: 50px; }
  .card--front { top: 514px; }

  .brand-name {
    font-weight: 400;
    font-size: 22px;
    letter-spacing: 3px;
    text-transform: uppercase;
    color: var(--ink);
    white-space: nowrap;
    position: absolute;
    left: 60px;
  }

  /* back side */
  .card--back .brand-name { top: 250px; }
  .services {
    position: absolute;
    left: 450px;
    top: 110px;
  }
  .services__title {
    font-weight: 800;
    font-size: 17px;
    letter-spacing: 0.5px;
    margin-bottom: 8px;
  }
  .services__list { list-style: none; }
  .services__item {
    display: flex;
    align-items: center;
    gap: 8px;
    font-size: 15px;
    line-height: 24px;
    white-space: nowrap;
  }
  .tick { width: 13px; height: 13px; flex: none; }

  /* front side */
  .card--front .brand-name { top: 72px; }
  .contact {
    position: absolute;
    left: 60px;
    top: 200px;
  }
  .contact__name {
    font-weight: 800;
    font-size: 38px;
    line-height: 1.1;
  }
  .contact__role {
    font-weight: 700;
    font-size: 17px;
    margin-top: 6px;
    padding-bottom: 14px;
    border-bottom: 1.5px solid var(--ink);
    width: 280px;
  }
  .contact__line {
    display: flex;
    align-items: center;
    gap: 14px;
    font-size: 19px;
    margin-top: 14px;
  }
  .icon { width: 18px; height: 18px; flex: none; }
</style>
</head>
<body>

<section class="card card--back" aria-label="Card back">
  <div class="brand-name">Harborline Builders</div>
  <div class="services">
    <h2 class="services__title">OUR SERVICES</h2>
    <ul class="services__list">
      <li class="services__item"><svg class="tick" viewBox="0 0 13 13"><rect x="0.75" y="0.75" width="11.5" height="11.5" fill="none" stroke="#fff" stroke-width="1.5"/><path d="M3 6.5l2.5 2.5L10 3.5" fill="none" stroke="#fff" stroke-width="1.8"/></svg>Remodel: Kitchen &amp; Bath</li>
      <li class="services__item"><svg class="tick" viewBox="0 0 13 13"><rect x="0.75" y="0.75" width="11.5" height="11.5" fill="none" stroke="#fff" stroke-width="1.5"/><path d="M3 6.5l2.5 2.5L10 3.5" fill="none" stroke="#fff" stroke-width="1.8"/></svg>Painting: Interior &amp; Exterior</li>
      <li class="services__item"><svg class="tick" viewBox="0 0 13 13"><rect x="0.75" y="0.75" width="11.5" height="11.5" fill="none" stroke="#fff" stroke-width="1.5"/><path d="M3 6.5l2.5 2.5L10 3.5" fill="none" stroke="#fff" stroke-width="1.8"/></svg>Flooring: Carpet, Vinyl, Wood</li>
      <li class="services__item"><svg class="tick" viewBox="0 0 13 13"><rect x="0.75" y="0.75" width="11.5" height="11.5" fill="none" stroke="#fff" stroke-width="1.5"/><path d="M3 6.5l2.5 2.5L10 3.5" fill="none" stroke="#fff" stroke-width="1.8"/></svg>Window &amp; Door Replacement</li>
      <li class="services__item"><svg class="tick" viewBox="0 0 13 13"><rect x="0.75" y="0.75" width="11.5" height="11.5" fill="none" stroke="#fff" stroke-width="1.5"/><path d="M3 6.5l2.5 2.5L10 3.5" fill="none" stroke="#fff" stroke-width="1.8"/></svg>Plumbing: Repairs &amp; Upgrades</li>
      <li class="services__item"><svg class="tick" viewBox="0 0 13 13"><rect x="0.75" y="0.75" width="11.5" height="11.5" fill="none" stroke="#fff" stroke-width="1.5"/><path d="M3 6.5l2.5 2.5L10 3.5" fill="none" stroke="#fff" stroke-width="1.8"/></svg>Energy- Efficient Upgrades</li>
      <li class="services__item"><svg class="tick" viewBox="0 0 13 13"><rect x="0.75" y="0.75" width="11.5" height="11.5" fill="none" stroke="#fff" stroke-width="1.5"/><path d="M3 6.5l2.5 2.5L10 3.5" fill="none" stroke="#fff" stroke-width="1.8"/></svg>Deck &amp; Patio Construction</li>
    </ul>
  </div>
</section>

<section class="card card--front" aria-label="Card front">
  <div class="brand-name">Harborline Builders</div>
  <div class="contact">
    <h1 class="contact__name">Marcus Delling</h1>
    <p class="contact__role">Licensed General Contractors</p>
    <p class="contact__line">
      <svg class="icon" viewBox="0 0 18 18"><circle cx="9" cy="9" r="9" fill="#fff"/><path d="M6 4.5c-.8.4-1.4 1.2-1.2 2.4.5 2.6 3.5 5.8 6.3 6.3 1.1.2 2-.4 2.4-1.2l-1.8-1.4-1.1.8c-1.2-.5-2.5-1.8-3-3l.8-1.1z" fill="#121212"/></svg>
      858-471-6093
    </p>
    <p class="contact__line">
      <svg class="icon" viewBox="0 0 18 18"><circle cx="9" cy="9" r="9" fill="#fff"/><g fill="none" stroke="#121212" stroke-width="1.2"><circle cx="9" cy="9" r="5.5"/><ellipse cx="9" cy="9" rx="2.4" ry="5.5"/><path d="M3.5 9h11"/></g></svg>
      www.brightoakbuilders.com
    </p>
  </div>
</section>

</body>
</html>
```